Dwelvano - "Where Pest Control is Free for Life..." Please see pitch deck...

Project goal, that this is a reusable template, not a one-off card
Brand and design direction, follow the logo, use the brand palette (with a color swatch table), typography and layout guidance
The John Doe placeholder content as a clean field-by-field table (name, title, company, address, office, cell, fax, email, dwelvano.com)
Print specs, 3.5 × 2 in trim, 0.125 in bleed, 300 DPI, CMYK, crop marks
Deliverables, layered editable PSD (your primary ask) plus vector .AI/.EPS and a press-ready PDF/X-1a, with fonts packaged
What you'll provide (logo, colors, fonts)
Process and sign-off, concept first, then full file package on approval.
Populate every field with this John Doe placeholder data so we can see the layout fully built out. We will replace it per person.
Name John Doe
Title Title / Position
Company Dwelvano
Address 123 Main Street, Suite 100, Tallahassee, FL 32301
Office (850) 555-0100
Cell (850) 555-0123
Fax (850) 555-0199
Email johndoe@dwelvano.com
Website dwelvano.com

We need the working, editable source files so we can update them ourselves, plus a ready-to-print export:
1. Photoshop (.PSD) — fully layered and editable, with each contact field on its own labeled text layer. This is the primary requested format.
2. Vector source — the press-standard editable format, Adobe Illustrator (.AI) and/or .EPS, since vector is preferred for crisp text and logos at print.
3. Print-ready PDF — press-quality (PDF/X-1a), CMYK, with bleed and crop marks, both sides.
4. Packaged fonts and links — include or list all fonts used, and package any linked assets so the files open correctly on our end.

Why both PSD and vector
The PSD covers our request directly and is easy for us to edit. Vector (.AI/.EPS) is what most commercial printers actually prefer for type and logos because it stays razor-sharp at any size. Providing both keeps us flexible no matter which printer we use. Have fun and keep it modern and cool the designer of the logo did a great job, see what you can do.

```html
<!DOCTYPE html>
<html lang="en">
<head>
<meta charset="utf-8">
<title>Dwelvano Business Card</title>
<link href="https://fonts.googleapis.com/css2?family=Montserrat:wght@500;600;800&family=Lato:wght@400&display=swap" rel="stylesheet">
<style>
  :root {
    --stage: #1c1c1c;
    --card: #000000;
    --teal: #0bb1c4;
    --white: #ffffff;
    --ink: #111111;
  }
  * { margin: 0; padding: 0; box-sizing: border-box; }
  html, body { width: 1200px; height: 1059px; overflow: hidden; background: var(--stage); }
  .stage { position: relative; width: 1200px; height: 1059px; }

  .card {
    position: absolute;
    left: 254px;
    width: 691px;
    height: 394px;
    background: var(--card);
    border-radius: 16px;
    overflow: hidden;
  }
  .card--front { top: 87px; }
  .card--back { top: 550px; }

  .brand {
    position: absolute;
    display: flex;
    align-items: center;
    gap: 10px;
    font-family: "Montserrat", sans-serif;
    font-weight: 800;
    color: var(--white);
    letter-spacing: -1px;
    line-height: 1;
  }
  .brand__mark { background: var(--teal); flex: none; }
  .card--front .brand { right: 26px; top: 42px; font-size: 58px; }
  .card--front .brand__mark { width: 16px; height: 16px; }
  .card--back .brand { left: 50%; top: 50%; transform: translate(-50%, -50%); font-size: 74px; }
  .card--back .brand__mark { width: 20px; height: 20px; }

  .person { position: absolute; left: 27px; top: 210px; font-family: "Montserrat", sans-serif; }
  .person__name { font-weight: 600; font-size: 27px; color: var(--teal); letter-spacing: 0.5px; line-height: 1; }
  .person__title { font-weight: 500; font-size: 18px; color: var(--white); margin-top: 8px; letter-spacing: 0.5px; }

  .divider { position: absolute; left: 27px; top: 276px; width: 625px; height: 1.5px; background: var(--white); }

  .contact { position: absolute; font-family: "Lato", sans-serif; font-size: 18.5px; color: var(--white); line-height: 1; }
  .contact__row { display: flex; align-items: center; gap: 9px; height: 28px; white-space: nowrap; }
  .contact__icon { width: 16px; height: 16px; flex: none; fill: var(--teal); }
  .contact--phones { left: 27px; top: 290px; }
  .contact--fax-email { left: 204px; top: 287px; }
  .contact--fax-email .contact__icon { width: 18px; }
  .contact--address { left: 435px; top: 290px; line-height: 25px; }

  .band { position: absolute; left: 0; bottom: 0; width: 691px; height: 30px; }
  .band__url {
    position: absolute; left: 416px; right: 0; bottom: 7px;
    text-align: center; font-family: "Lato", sans-serif; font-size: 18px; color: var(--ink);
    padding-left: 30px;
  }
</style>
</head>
<body>
<main class="stage">
  <section class="card card--front" aria-label="Business card front">
    <div class="brand"><span>Dwelvano</span><span class="brand__mark"></span></div>

    <div class="person">
      <p class="person__name">JOHN DOE</p>
      <p class="person__title">Owner</p>
    </div>

    <div class="divider"></div>

    <div class="contact contact--phones">
      <p class="contact__row">
        <svg class="contact__icon" viewBox="0 0 16 16" aria-hidden="true"><path d="M1 5c0-2 3-3 7-3s7 1 7 3v1.5h-3.5V5h-7v1.5H1z"/><path d="M4 7.5h8l2 5.5v2H2v-2z"/></svg>
        (850) 555-0100
      </p>
      <p class="contact__row">
        <svg class="contact__icon" viewBox="0 0 16 16" aria-hidden="true"><path d="M4 0h8a1 1 0 0 1 1 1v14a1 1 0 0 1-1 1H4a1 1 0 0 1-1-1V1a1 1 0 0 1 1-1zm.5 2v10h7V2zM8 13a.9.9 0 1 0 0 1.8A.9.9 0 0 0 8 13z"/></svg>
        (850) 555-0123
      </p>
    </div>

    <div class="contact contact--fax-email">
      <p class="contact__row">
        <svg class="contact__icon" viewBox="0 0 18 16" aria-hidden="true"><rect x="0" y="3" width="3" height="13"/><path d="M4 5h14v11H4z"/><path d="M7 0h8v4H7z"/><rect x="7" y="8" width="2" height="2" fill="#000"/><rect x="11" y="8" width="2" height="2" fill="#000"/><rect x="7" y="12" width="2" height="2" fill="#000"/><rect x="11" y="12" width="2" height="2" fill="#000"/></svg>
        (850) 555-0199
      </p>
      <p class="contact__row">
        <svg class="contact__icon" viewBox="0 0 18 14" aria-hidden="true"><path d="M0 1h18v1L9 8 0 2z"/><path d="M0 4l9 6 9-6v10H0z"/></svg>
        johndoe@dwelvano.com
      </p>
    </div>

    <address class="contact contact--address" style="font-style:normal">
      123 Main Street, Suite 100,<br>Tallahassee, FL 32301
    </address>

    <svg class="band" viewBox="0 0 691 30" preserveAspectRatio="none" aria-hidden="true">
      <path d="M0 9h393l-9 9H0z" fill="var(--teal)"/>
      <path d="M0 22h382l-8 8H0z" fill="var(--teal)"/>
      <path d="M416 0H691V30H385z" fill="var(--teal)"/>
    </svg>
    <p class="band__url">www.dwelvano.com</p>
  </section>

  <section class="card card--back" aria-label="Business card back">
    <div class="brand"><span>Dwelvano</span><span class="brand__mark"></span></div>
  </section>
</main>
</body>
</html>
```